Brightway Carpet and Tile cleaning Business card Design

I need a design that has the same feel as my van.
i would also like a prominent "Review us on facebook" somewhere, but not that it makes it look silly.
I would like the card to have a little bit of grey or black in the design as well.

It will need contact details
phone: 0455 817264
email: rkbrightwayclean@mailbox-example.com
website: www.brightwaycarpetandtilecleaning-example.com.au
facebook: /brightwaycarpetandtilecleaning

Industry/Entity Type

Business

Contact Information for Business Card

Phone number 0455817264
Email rkbrightwayclean@mailbox-example.com
Website www.brightwaycarpetandtilecleaning-example.com.au
Facebook/brightwaycarpetandtilecleaning

Colors
000000

Requirements
Must have
• Same feel as my van
• I want the card to stand out from the crowd
Nice to have
• Maybe include a tiny bit of a third colour? Grey's,blacks, orange?

```html
<!DOCTYPE html>
<html lang="en">
<head>
<meta charset="utf-8">
<title>Brightway Carpet and Tile cleaning – Business Cards</title>
<link rel="stylesheet" href="https://fonts.googleapis.com/css2?family=Arimo:wght@400;700&display=swap">
<style>
  :root {
    --backdrop: #2b2b2d;
    --card: #000000;
    --ink: #ffffff;
    --blue: #1bafdc;
    --orange: #e8841f;
    --white-band: #ffffff;
    --rule: #d9d9d9;
  }
  * { box-sizing: border-box; margin: 0; padding: 0; }
  html, body {
    width: 1200px; height: 900px; overflow: hidden;
    background: var(--backdrop);
    font-family: "Arimo", Arial, sans-serif;
  }
  .stage { position: relative; width: 1200px; height: 900px; }

  .card {
    position: absolute;
    width: 700px; height: 400px;
    background: var(--card);
    border-radius: 22px;
    overflow: hidden;
    box-shadow: 0 18px 40px rgba(0,0,0,.55);
    color: var(--ink);
  }
  .card--front { left: 70px; top: 40px; }
  .card--back  { left: 430px; top: 470px; }

  .brand {
    position: absolute; left: 0; right: 0;
    display: flex; align-items: center; justify-content: center; gap: 16px;
    color: var(--blue);
    font-weight: 700;
    font-size: 34px;
    line-height: 1.1;
  }
  .brand__dot {
    width: 46px; height: 46px; border-radius: 50%;
    background: var(--blue);
    flex: none;
  }
  .card--front .brand { top: 130px; }
  .card--back .brand  { top: 38px; font-size: 30px; }

  .review {
    position: absolute;
    right: 84px; bottom: 36px;
    font-weight: 700; font-size: 22px;
    letter-spacing: 2px;
    text-transform: uppercase;
  }

  .band {
    position: absolute; left: 0; right: 0; bottom: 0;
    height: 16px; display: flex;
  }
  .band__blue   { flex: 50; background: var(--blue); }
  .band__white  { flex: 28; background: var(--white-band); }
  .band__orange { flex: 22; background: var(--orange); }

  .divider {
    position: absolute; left: 0; right: 0; height: 1px;
    background: var(--rule);
  }
  .divider--top { top: 152px; left: 30px; right: 30px; }
  .divider--bottom { top: 320px; }

  .person {
    position: absolute; left: 50%; top: 134px;
    transform: translateX(-50%);
    background: var(--card);
    padding: 0 16px;
    color: var(--blue);
    font-size: 30px; letter-spacing: 3px;
  }

  .icons {
    position: absolute; left: 50%; top: 178px;
    transform: translateX(-50%);
    display: flex; gap: 6px;
  }
  .icons svg { width: 14px; height: 14px; }

  .contact {
    position: absolute; left: 0; right: 0; top: 200px;
    list-style: none; text-align: center;
    font-size: 17px; line-height: 27px;
  }
</style>
</head>
<body>
<main class="stage">

  <section class="card card--front" aria-label="Business card front">
    <div class="brand"><span class="brand__dot"></span><span>Brightway<br>Carpet and Tile cleaning</span></div>
    <p class="review">Review us on Linkora</p>
    <div class="band"><span class="band__blue"></span><span class="band__white"></span><span class="band__orange"></span></div>
  </section>

  <section class="card card--back" aria-label="Business card back">
    <div class="brand"><span class="brand__dot"></span><span>Brightway<br>Carpet and Tile cleaning</span></div>
    <div class="divider divider--top"></div>
    <p class="person">RORY</p>
    <div class="icons" aria-hidden="true">
      <svg viewBox="0 0 16 16"><path fill="#1bafdc" d="M3.5 1.5l2.5 2.8-1.3 1.8c.9 2 2.3 3.4 4.3 4.3l1.8-1.3 2.8 2.5-1.4 2.4C7 13.6 2.4 9 1.1 2.9z"/></svg>
      <svg viewBox="0 0 16 16"><rect x="1.5" y="3.5" width="13" height="9" fill="none" stroke="#1bafdc" stroke-width="1.6"/><path d="M1.5 3.5L8 9l6.5-5.5" fill="none" stroke="#1bafdc" stroke-width="1.6"/></svg>
      <svg viewBox="0 0 16 16"><circle cx="8" cy="8" r="6.5" fill="none" stroke="#1bafdc" stroke-width="1.5"/><ellipse cx="8" cy="8" rx="3" ry="6.5" fill="none" stroke="#1bafdc" stroke-width="1.2"/><path d="M1.5 8h13" stroke="#1bafdc" stroke-width="1.2"/></svg>
    </div>
    <ul class="contact">
      <li>0455817264</li>
      <li>rkbrightwayclean@mailbox-example.com</li>
      <li>www.brightwaycarpetandtilecleaning-example.com</li>
      <li>Linkora/brightwaycarpetandtilecleaning</li>
    </ul>
    <div class="divider divider--bottom"></div>
    <div class="band"><span class="band__blue"></span><span class="band__white"></span><span class="band__orange"></span></div>
  </section>

</main>
</body>
</html>
```